Law Offices business card

Hi there, I'll need business card for the Law Offices of Colin Matheny. The information must convey his strategic approach and quick resolution to complex business litigation needs. Please emphasize Civil Litigation, Corporate Law, Business Governance and Real Estate Law. Colin has over 25 years of experience in these fields.The card should be modern and edgy and the message should be clear. Please consult his current website for ideas.

```html
<!DOCTYPE html>
<html lang="en">
<head>
<meta charset="utf-8">
<title>Law Offices of Colin Matheny – Business Card</title>
<link rel="stylesheet" href="https://fonts.googleapis.com/css2?family=Source+Sans+3:wght@400;600;700&display=swap">
<style>
  :root {
    --backdrop: #3b342f;
    --card: #151515;
    --card-sheen: #2a2a2a;
    --orange: #ff6a0d;
    --white: #ffffff;
    --grey: #c9c9c9;
  }
  * { box-sizing: border-box; margin: 0; padding: 0; }
  html, body { width: 1200px; height: 844px; overflow: hidden; }
  body {
    background: var(--backdrop);
    font-family: "Source Sans 3", "Helvetica Neue", Arial, sans-serif;
    color: var(--white);
    position: relative;
  }
  .card {
    position: absolute;
    top: 273px;
    width: 520px;
    height: 297px;
    background: radial-gradient(ellipse at 60% 35%, var(--card-sheen), var(--card) 70%);
    overflow: hidden;
  }
  .card--contact { left: 50px; }
  .card--brand { left: 630px; }

  /* Contact side */
  .band {
    position: absolute;
    left: 0;
    width: 100%;
    height: 11px;
    background: var(--orange);
  }
  .band--top { top: 26px; }
  .band--bottom { top: 262px; }
  .contact {
    position: absolute;
    left: 0;
    right: 0;
    top: 56px;
    text-align: center;
    padding-left: 70px;
  }
  .contact__name {
    display: inline-block;
    color: var(--orange);
    font-weight: 700;
    font-size: 19px;
    letter-spacing: 0.3px;
    text-transform: uppercase;
    border-bottom: 1px solid var(--orange);
    padding: 0 6px 1px;
  }
  .contact__role { font-size: 13px; margin-top: 2px; }
  .contact__lines {
    list-style: none;
    margin-top: 22px;
    font-size: 14.5px;
    line-height: 19px;
  }
  .contact__address {
    position: absolute;
    left: 0;
    right: 0;
    top: 226px;
    text-align: center;
    font-size: 15px;
    white-space: pre;
  }

  /* Brand side */
  .tab {
    position: absolute;
    width: 30px;
    height: 22px;
    background: var(--orange);
  }
  .tab::after {
    content: "";
    position: absolute;
    top: 0;
    right: 0;
    width: 5px;
    height: 100%;
    background: var(--white);
  }
  .tab--right { right: 0; top: 30px; }
  .tab--left { left: 0; top: 172px; }
  .firm {
    position: absolute;
    left: 96px;
    top: 84px;
    display: flex;
    align-items: center;
    gap: 16px;
  }
  .firm__dot {
    width: 62px;
    height: 62px;
    border-radius: 50%;
    background: var(--orange);
    border: 3px solid var(--grey);
    flex: none;
  }
  .firm__name {
    color: var(--orange);
    font-weight: 600;
    font-size: 22px;
    line-height: 25px;
    text-transform: uppercase;
    letter-spacing: 0.5px;
  }
  .practice {
    position: absolute;
    left: 0;
    right: 0;
    top: 170px;
    text-align: center;
    font-weight: 700;
    font-size: 15px;
    line-height: 22px;
    padding-left: 50px;
  }
  .practice__experience {
    color: var(--orange);
    font-weight: 600;
    font-size: 13.5px;
    margin-top: 4px;
  }
</style>
</head>
<body>
  <section class="card card--contact" aria-label="Contact side of the card">
    <div class="band band--top"></div>
    <div class="contact">
      <h1 class="contact__name">Colin Matheny</h1>
      <p class="contact__role">Attorney</p>
      <ul class="contact__lines">
        <li>561-555-0142</li>
        <li>561-555-0187</li>
        <li>colin@mathenylaw.com</li>
        <li>www.mathenylaw.com</li>
      </ul>
    </div>
    <p class="contact__address">118B Coral Avenue  Palm Beach, Florida 33480</p>
    <div class="band band--bottom"></div>
  </section>

  <section class="card card--brand" aria-label="Firm side of the card">
    <div class="tab tab--right"></div>
    <div class="tab tab--left"></div>
    <div class="firm">
      <span class="firm__dot"></span>
      <h2 class="firm__name">Law Offices<br>of Colin Matheny</h2>
    </div>
    <div class="practice">
      <p>Civil Litigation &nbsp;|&nbsp; Corporate Law</p>
      <p>Business Governance &nbsp;|&nbsp; Real Estate Law</p>
      <p class="practice__experience">Over 25 Years of Experience</p>
    </div>
  </section>
</body>
</html>
```